I need an amazing business card!

I am the principle in my own software company that develops zorPad and mobile applications. I require a great business card design. I've attached my corporate logo (Thanks Tomas!).
I would like the design to integrate the logo, my name, email address and skype account:
name Brent Olafsen
email brentolafsen@tavrik.com
skype brentolafsen.net
I would like the back of the card to have a "write on me area" similar to the "write on me" card on this page, row 6:
http://us.prindlewick.com/design-templates/business-cards/#industry=Computing%20%26%20IT
As far as the rest - it's all you!
Updates
1) Please add an example telephone number as well.
Industry/Entity Type
Software
Look and feel
Each slider illustrates characteristics of the customer's brand and the style your logo design should communicate.

```html
<!DOCTYPE html>
<html lang="en">
<head>
<meta charset="utf-8">
<title>Brent Olafsen – Business Card</title>
<link rel="stylesheet" href="https://fonts.googleapis.com/css2?family=Poppins:wght@300;700&display=swap">
<style>
  :root {
    --yellow-top: #fbcf00;
    --yellow-mid: #ffe600;
    --yellow-bottom: #f8c600;
    --olive: #c8c61c;
    --olive-line: #9aa51e;
    --ink: #5a5a5a;
    --pale: #fff27a;
  }
  html, body {
    margin: 0;
    padding: 0;
    overflow: hidden;
    background: #ffffff;
  }
  .card {
    position: relative;
    width: 686px;
    height: 1200px;
    overflow: hidden;
    background: linear-gradient(170deg, var(--yellow-top) 0%, var(--yellow-mid) 48%, var(--yellow-bottom) 100%);
    font-family: "Poppins", sans-serif;
    color: var(--ink);
  }
  .brand-mark {
    position: absolute;
    left: 0;
    top: 0;
  }
  .brand-name {
    position: absolute;
    right: 40px;
    top: 760px;
    margin: 0;
    font-weight: 700;
    font-size: 44px;
    color: var(--pale);
  }
  .identity {
    position: absolute;
    left: 36px;
    top: 46px;
  }
  .identity__name {
    margin: 0;
    font-weight: 700;
    font-size: 60px;
    line-height: 1;
    letter-spacing: -0.5px;
  }
  .identity__title {
    margin: 4px 0 0;
    font-weight: 300;
    font-size: 40px;
    line-height: 1.1;
  }
  .contacts {
    position: absolute;
    left: 36px;
    top: 428px;
    margin: 0;
    padding: 0;
    list-style: none;
  }
  .contacts__item {
    display: flex;
    align-items: center;
    height: 77px;
    white-space: nowrap;
  }
  .contacts__icon {
    width: 64px;
    height: 52px;
    margin-right: 78px;
    flex: none;
  }
  .contacts__text {
    font-weight: 700;
    font-size: 36px;
    letter-spacing: -0.3px;
  }
</style>
</head>
<body>
  <div class="card">
    <svg class="brand-mark" width="686" height="1200" viewBox="0 0 686 1200" role="img" aria-label="Large Tavrik brand circle decoration">
      <circle cx="560" cy="520" r="420" fill="var(--olive)" opacity="0.85"/>
    </svg>
    <p class="brand-name">Tavrik</p>

    <header class="identity">
      <h1 class="identity__name">Brent Olafsen</h1>
      <p class="identity__title">Principle</p>
    </header>

    <ul class="contacts">
      <li class="contacts__item">
        <svg class="contacts__icon" viewBox="0 0 64 52" fill="none" stroke="var(--olive-line)" stroke-width="2.2" stroke-linejoin="round">
          <path d="M4 18 C4 6 60 6 60 18 L60 22 L46 22 L46 16 C40 13 24 13 18 16 L18 22 L4 22 Z"/>
          <path d="M16 24 L48 24 L56 46 L8 46 Z"/>
          <circle cx="32" cy="35" r="6.5"/>
        </svg>
        <span class="contacts__text">317 555-0148</span>
      </li>
      <li class="contacts__item">
        <svg class="contacts__icon" viewBox="0 0 64 52" fill="none" stroke="var(--olive-line)" stroke-width="2.2" stroke-linejoin="round">
          <rect x="3" y="10" width="58" height="34"/>
          <path d="M3 10 L32 32 L61 10"/>
          <path d="M3 44 L24 26 M61 44 L40 26"/>
        </svg>
        <span class="contacts__text">brentolafsen@tavrik.com</span>
      </li>
      <li class="contacts__item">
        <svg class="contacts__icon" viewBox="0 0 64 52" fill="none" stroke="var(--olive-line)" stroke-width="2.2">
          <circle cx="26" cy="26" r="21"/>
        </svg>
        <span class="contacts__text">brentolafsen.net</span>
      </li>
      <li class="contacts__item">
        <svg class="contacts__icon" viewBox="0 0 64 52" fill="none" stroke="var(--olive-line)" stroke-width="2" stroke-linejoin="round">
          <path d="M2 16 L8 30 L13 18 L18 30 L24 16 M22 16 L28 30 L33 18 L38 30 L44 16 M42 16 L48 30 L53 18 L58 30 L63 16"/>
          <path d="M40 22 L40 46 L45 41 L49 50 L53 48 L49 39 L56 39 Z" fill="var(--yellow-mid)"/>
        </svg>
        <span class="contacts__text">www.tavrik.com</span>
      </li>
    </ul>
  </div>
</body>
</html>
```